Basic business card

use my newly created logo - and the phrases (Lower Cost of Test & Accelarated New Product Introduction) - and my new email domain / ID - use at conferences / tradeshows

Industry/Entity Type

semiconductor

Contact Information for Business Card

Daniel K Forde, Owner, communicate via Logo - Lower COT - Cost of Test, Accelerated NPI - New Product Introduction, phone +1 555 613 0946, Chandler, Arizona, USA, daniel.forde@qal-vub.com

Font styles to use
Sans Serif

Requirements
Nice to have
• re-use my logo created via Pixel Harbor last August (#7315926)

```html
<!DOCTYPE html>
<html lang="en">
<head>
<meta charset="utf-8">
<title>QAL-VUB Business Card</title>
<link rel="stylesheet" href="https://fonts.googleapis.com/css2?family=Open+Sans:wght@400;600;700&display=swap">
<style>
  :root {
    --backdrop: #333333;
    --card-dark: #1f1f23;
    --card-back: #222226;
    --emboss: #141417;
    --band-orange: #f39a1f;
    --name-orange: #f39a1f;
    --name-green: #7cc243;
    --slate: #4a5470;
    --white: #ffffff;
    --icon-blue: #3fb9e6;
  }
  * { margin: 0; padding: 0; box-sizing: border-box; }
  html, body {
    width: 1200px; height: 780px; overflow: hidden;
    background: var(--backdrop);
    font-family: "Open Sans", sans-serif;
  }
  .card {
    position: absolute; top: 230px;
    width: 560px; height: 320px;
    overflow: hidden;
  }

  /* Back side */
  .card-back { left: 30px; background: var(--card-back); }
  .back-brand {
    position: absolute; left: 0; right: 0; top: 0; bottom: 0;
    display: flex; align-items: center; justify-content: center; gap: 16px;
  }
  .back-brand-mark { width: 44px; height: 44px; background: var(--emboss); }
  .back-brand-name {
    font-size: 64px; font-weight: 400; letter-spacing: 2px;
    color: var(--emboss); line-height: 1;
  }

  /* Front side */
  .card-front { left: 610px; background: var(--card-dark); }
  .info-band {
    position: absolute; left: 0; right: 0; bottom: 0; height: 148px;
    background: var(--band-orange);
  }
  .symbol-area {
    position: absolute; left: 16px; bottom: 14px;
    width: 128px; height: 128px;
    background: var(--slate);
  }
  .brand {
    position: absolute; left: 24px; top: 112px;
    display: flex; align-items: center; gap: 10px;
  }
  .brand-mark { width: 22px; height: 22px; background: var(--slate); }
  .brand-name {
    font-size: 40px; font-weight: 400; letter-spacing: 1px;
    color: var(--slate); line-height: 1;
  }
  .identity { position: absolute; right: 36px; top: 18px; text-align: right; }
  .person-name { font-size: 30px; font-weight: 700; letter-spacing: 1px; line-height: 1.15; }
  .person-name .first { color: var(--name-orange); }
  .person-name .last { color: var(--name-green); }
  .person-role { font-size: 14px; font-weight: 600; color: var(--white); letter-spacing: 0.8px; }
  .accent-bar {
    position: absolute; right: 10px; top: 16px; width: 16px; height: 54px;
    background: var(--band-orange);
  }
  .contact {
    position: absolute; right: 18px; bottom: 16px;
    color: var(--white); text-align: right;
    font-size: 13px; font-weight: 600; letter-spacing: 0.6px; line-height: 1.45;
  }
  .contact .row { display: flex; justify-content: flex-end; align-items: center; gap: 8px; }
  .contact .address { margin-bottom: 6px; }
  .icon { width: 13px; height: 13px; flex: none; }
  .icon-spacer { width: 13px; flex: none; }
</style>
</head>
<body>
  <div class="card card-back">
    <div class="back-brand">
      <div class="back-brand-mark"></div>
      <div class="back-brand-name">QAL-VUB</div>
    </div>
  </div>

  <div class="card card-front">
    <div class="info-band"></div>
    <div class="symbol-area" role="img" aria-label="Large company symbol area"></div>
    <div class="accent-bar"></div>

    <div class="identity">
      <div class="person-name"><span class="first">Lena</span> <span class="last">Varga</span></div>
      <div class="person-role">Managing Director</div>
    </div>

    <div class="brand">
      <div class="brand-mark"></div>
      <div class="brand-name">QAL-VUB</div>
    </div>

    <div class="contact">
      <div class="address">
        <div class="row"><span>1480 Meadowlark Ave. Suite 310</span><span class="icon-spacer"></span></div>
        <div class="row"><span>Chandler, AZ 85226</span><span class="icon-spacer"></span></div>
      </div>
      <div class="row"><span>(555) 271-4863</span>
        <svg class="icon" viewBox="0 0 24 24" aria-hidden="true"><path fill="var(--icon-blue)" d="M6.6 10.8a15 15 0 0 0 6.6 6.6l2.2-2.2c.3-.3.7-.4 1-.2 1.1.4 2.3.6 3.6.6.6 0 1 .4 1 1V20c0 .6-.4 1-1 1A17 17 0 0 1 3 4c0-.6.4-1 1-1h3.5c.6 0 1 .4 1 1 0 1.3.2 2.5.6 3.6.1.3 0 .7-.2 1z"/></svg>
      </div>
      <div class="row"><span>info@qal-vub.com</span>
        <svg class="icon" viewBox="0 0 24 24" aria-hidden="true"><rect x="2" y="5" width="20" height="14" rx="2" fill="var(--icon-blue)"/><path d="M3 6l9 7 9-7" fill="none" stroke="var(--band-orange)" stroke-width="1.8"/></svg>
      </div>
      <div class="row"><span>www.qal-vub.com</span>
        <svg class="icon" viewBox="0 0 24 24" aria-hidden="true"><circle cx="12" cy="12" r="10" fill="var(--icon-blue)"/><g fill="none" stroke="var(--band-orange)" stroke-width="1.4"><ellipse cx="12" cy="12" rx="4.5" ry="10"/><path d="M2 12h20M4 7h16M4 17h16"/></g></svg>
      </div>
    </div>
  </div>
</body>
</html>
```